Namecard Designs+Logo for a High End Automobile Company

We need a new business card for our company called Nordel Motorwerk.

www.nordelmotorwerk.example.sg
Our new website will be up in 2.5 months time.

We sell used and brand new continental cars like Valcrest, KTR, Almira, Dunvale and etc. Currently we are operating from 2 offices in Singapore and United Kingdom.

We want a design which is serious. We are open to colours but try to keep it at a maximum of 3 colours.

We prefer something simple and minimal. We are open to 2 sides printing or even 2 sided namecards. Both UK and Singapore company offices address must be in; either side by side, front and back, or even 2 sided cards.

The logo can be a text logo, emblem, abstract, pictorial or combination.

We are printing with Printlyx.com so please kindly follow the printing guideline.

http://uk.printlyx.example/help/faq/templates-and-guidelines.html

Rich and Car Enthusiasts

Printing

• Our 2 offices; UK and Singapore.

Our slogan which is " The Automobile Specialist"
• Not more than 3 colours

```html
<!DOCTYPE html>
<html lang="en">
<head>
<meta charset="utf-8">
<title>Nordel Motorwerk — Business Cards</title>
<link rel="stylesheet" href="https://fonts.googleapis.com/css2?family=Arimo:wght@400;700&family=Tinos:wght@400;700&display=swap">
<style>
  :root {
    --stage: #3b3b3d;
    --card-white: #ffffff;
    --brand-blue: #1f72c2;
    --brand-blue-light: #2f88d8;
    --brand-navy: #2a2f6c;
    --text-blue: #2a6db3;
    --text-grey: #6b6b6b;
    --mark-tone: #8fd3e6;
  }
  html, body {
    margin: 0; padding: 0;
    width: 1200px; height: 900px;
    overflow: hidden;
    background: var(--stage);
  }
  .stage { position: relative; width: 1200px; height: 900px; }

  .card { position: absolute; box-sizing: border-box; overflow: hidden; }
  .card--singapore {
    left: 27px; top: 60px; width: 561px; height: 308px;
    background: linear-gradient(135deg, var(--brand-blue-light), var(--brand-blue));
    color: #ffffff;
  }
  .card--uk {
    left: 613px; top: 60px; width: 561px; height: 312px;
    background: var(--card-white);
    color: var(--text-blue);
  }
  .card--front {
    left: 211px; top: 468px; width: 681px; height: 377px;
    background: var(--card-white);
  }

  .lockup { position: absolute; text-align: center; top: 22px; }
  .lockup__square {
    display: block; margin: 0 auto 16px;
    width: 54px; height: 62px;
    background: var(--mark-tone);
  }
  .lockup__name {
    font-family: "Arimo", Arial, sans-serif;
    font-weight: 700; font-size: 18px;
    white-space: nowrap;
  }
  .card--singapore .lockup { left: 30px; }
  .card--singapore .lockup__name { color: #ffffff; }
  .card--uk .lockup { right: 30px; }
  .card--uk .lockup__name { color: var(--brand-navy); }

  .faint-square {
    position: absolute; left: 355px; top: 25px;
    width: 185px; height: 255px;
    background: rgba(255,255,255,0.07);
  }

  .contact {
    position: absolute; left: 14px; top: 172px;
    margin: 0; padding: 0; list-style: none;
    font-family: "Tinos", "Times New Roman", serif;
    font-size: 15px; line-height: 16.5px;
  }
  .contact li { display: flex; align-items: center; height: 16.5px; white-space: nowrap; }
  .contact .icon { width: 13px; height: 12px; margin-right: 12px; flex: none; }
  .contact .icon--none { visibility: hidden; }

  .front__square {
    position: absolute; left: 284px; top: 27px;
    width: 117px; height: 188px;
    background: linear-gradient(180deg, #a9e2ef, #3fa8cc);
  }
  .front__name {
    position: absolute; left: 0; right: 0; top: 226px;
    text-align: center;
    font-family: "Arimo", Arial, sans-serif;
    font-weight: 700; font-size: 41px; line-height: 46px;
    color: var(--brand-navy);
    letter-spacing: 0.5px;
  }
  .front__slogan {
    position: absolute; left: 0; right: 0; top: 272px;
    text-align: center;
    font-family: "Arimo", Arial, sans-serif;
    font-size: 21px; line-height: 24px; letter-spacing: 2.5px;
    color: #3a3a3a;
  }
  .front__rule {
    position: absolute; left: 0; top: 323px;
    width: 494px; height: 3px;
    background: var(--brand-blue);
  }
  .front__person { position: absolute; right: 27px; top: 306px; text-align: right; }
  .front__person-name {
    font-family: "Tinos", "Times New Roman", serif;
    font-weight: 700; font-size: 25px; line-height: 28px;
    color: var(--text-blue);
  }
  .front__person-role {
    font-family: "Tinos", "Times New Roman", serif;
    font-size: 16px; line-height: 20px;
    color: var(--text-grey);
  }
</style>
</head>
<body>
<svg width="0" height="0" style="position:absolute">
  <defs>
    <symbol id="i-home" viewBox="0 0 13 12"><path d="M1 6 L6.5 1 L12 6 M3 5 V11 H10 V5" fill="none" stroke="currentColor" stroke-width="1.4"/></symbol>
    <symbol id="i-mail" viewBox="0 0 13 12"><rect x="1" y="2.5" width="11" height="7.5" rx="1" fill="currentColor"/></symbol>
    <symbol id="i-web" viewBox="0 0 13 12"><circle cx="6.5" cy="6" r="5" fill="none" stroke="currentColor" stroke-width="1.3"/><path d="M1.5 6 H11.5 M6.5 1 V11" stroke="currentColor" stroke-width="1"/></symbol>
    <symbol id="i-phone" viewBox="0 0 13 12"><path d="M1 4 Q6.5 0 12 4 L10 5.5 L8.5 4 H4.5 L3 5.5 Z" fill="currentColor"/><rect x="3" y="6" width="7" height="5" rx="1" fill="currentColor"/></symbol>
    <symbol id="i-fax" viewBox="0 0 13 12"><rect x="3" y="1" width="7" height="4" fill="none" stroke="currentColor" stroke-width="1.2"/><rect x="1" y="5" width="11" height="6" rx="1" fill="currentColor"/></symbol>
    <symbol id="i-mobile" viewBox="0 0 13 12"><rect x="4" y="0.5" width="5" height="11" rx="1" fill="none" stroke="currentColor" stroke-width="1.3"/></symbol>
  </defs>
</svg>

<main class="stage">
  <section class="card card--singapore" aria-label="Card back, Singapore office">
    <div class="faint-square" role="img" aria-label="Faint brand emblem area"></div>
    <div class="lockup">
      <span class="lockup__square"></span>
      <span class="lockup__name">Nordel Motorwerk</span>
    </div>
    <ul class="contact">
      <li><svg class="icon"><use href="#i-home"/></svg>00 Tanjong Marrow Road #00-00</li>
      <li><svg class="icon icon--none"></svg>Singapore 000000</li>
      <li><svg class="icon"><use href="#i-mail"/></svg>yourname@nordelmotorwerk.example</li>
      <li><svg class="icon"><use href="#i-web"/></svg>www.nordelmotorwerk.example</li>
      <li><svg class="icon"><use href="#i-phone"/></svg>+65 0000 0184</li>
      <li><svg class="icon"><use href="#i-fax"/></svg>+65 0000 0190</li>
      <li><svg class="icon"><use href="#i-mobile"/></svg>+65 0000 0136</li>
    </ul>
  </section>

  <section class="card card--uk" aria-label="Card back, United Kingdom office">
    <div class="lockup">
      <span class="lockup__square"></span>
      <span class="lockup__name">Nordel Motorwerk</span>
    </div>
    <ul class="contact">
      <li><svg class="icon"><use href="#i-home"/></svg>00 Halbrook Lane, Ashfold</li>
      <li><svg class="icon icon--none"></svg>London AB0 0CD, United Kingdom</li>
      <li><svg class="icon"><use href="#i-mail"/></svg>yourname@nordelmotorwerk.example</li>
      <li><svg class="icon"><use href="#i-web"/></svg>www.nordelmotorwerk.example</li>
      <li><svg class="icon"><use href="#i-phone"/></svg>+44 0000 000184</li>
      <li><svg class="icon"><use href="#i-fax"/></svg>+44 0000 000190</li>
      <li><svg class="icon icon--none"></svg>+44 0000 000136</li>
    </ul>
  </section>

  <section class="card card--front" aria-label="Card front">
    <div class="front__square" role="img" aria-label="Brand emblem area"></div>
    <div class="front__name">Nordel Motorwerk</div>
    <div class="front__slogan">The Automobile Specialist</div>
    <div class="front__rule"></div>
    <div class="front__person">
      <div class="front__person-name">Your Name</div>
      <div class="front__person-role">Principal</div>
    </div>
  </section>
</main>
</body>
</html>
```